Label design for an exciting new Vodka brand

We need a label design for a dynamic new Vodka brand called 'Pale lantern drift Vodka'. It is a crisp and versatile liquid with a clean and smooth finish. It should appeal to 21-39 year olds, with a slight female skew. Colours, fonts and styles should be modern and relatively neutral - take inspiration from the brand pictures attached.

Target Market(s)

21-39 year olds, both male and female, but with a slight female skew

```html
<!DOCTYPE html>
<html lang="en">
<head>
<meta charset="utf-8">
<title>Pale lantern drift Vodka – Label</title>
<link rel="stylesheet" href="https://fonts.googleapis.com/css2?family=Josefin+Sans:wght@300&display=swap">
<style>
  :root {
    --canvas-bg: #fbe3f2;
    --label-pink: #e266b5;
    --label-pink-light: #ef8fcb;
    --plum: #7d1f5f;
    --stripe-a: #d94fa8;
    --stripe-b: #6e1450;
  }
  * { margin: 0; padding: 0; box-sizing: border-box; }
  html, body {
    width: 1200px;
    height: 1200px;
    overflow: hidden;
    background: var(--canvas-bg);
  }
  .canvas {
    position: relative;
    width: 1200px;
    height: 1200px;
  }
  .label {
    position: absolute;
    left: 272px;
    top: 88px;
    width: 656px;
    height: 1024px;
  }
  .accent-column {
    position: absolute;
    left: 10px;
    top: 0;
    width: 186px;
    height: 614px;
    background: linear-gradient(180deg, var(--label-pink), var(--label-pink-light));
  }
  .stripe-block { position: absolute; display: block; }
  .stripe-block--top { left: 339px; top: 64px; width: 317px; height: 134px; }
  .stripe-block--ticks { left: 90px; top: 890px; width: 134px; height: 118px; }
  .stripe-block--bottom { left: 10px; top: 992px; width: 333px; height: 80px; }

  .brand-name {
    position: absolute;
    right: 0;
    top: 240px;
    width: 656px;
    font-family: "Josefin Sans", sans-serif;
    font-weight: 300;
    color: var(--plum);
    text-transform: uppercase;
  }
  .brand-name__line {
    display: block;
    text-align: right;
    font-size: 88px;
    line-height: 112px;
    letter-spacing: 1px;
  }
  .brand-name__line--spirit {
    margin-top: 22px;
    text-align: left;
    font-size: 190px;
    line-height: 190px;
    letter-spacing: 12px;
  }
</style>
</head>
<body>
  <main class="canvas">
    <section class="label" aria-label="Pale lantern drift Vodka bottle label">
      <div class="accent-column"></div>

      <svg class="stripe-block stripe-block--top" viewBox="0 0 317 134" aria-hidden="true">
        <defs>
          <linearGradient id="stripeFade" x1="0" y1="0" x2="1" y2="0">
            <stop offset="0" stop-color="var(--stripe-a)"/>
            <stop offset="1" stop-color="var(--stripe-b)"/>
          </linearGradient>
        </defs>
        <g fill="url(#stripeFade)">
          <rect x="0" y="0" width="317" height="5"/>
          <rect x="0" y="16" width="317" height="5"/>
          <rect x="0" y="32" width="317" height="5"/>
          <rect x="0" y="48" width="317" height="5"/>
          <rect x="0" y="64" width="317" height="5"/>
          <rect x="0" y="80" width="317" height="5"/>
          <rect x="0" y="96" width="317" height="5"/>
          <rect x="0" y="112" width="317" height="5"/>
          <rect x="0" y="128" width="317" height="5"/>
        </g>
      </svg>

      <h1 class="brand-name">
        <span class="brand-name__line">Pale</span>
        <span class="brand-name__line">Lantern</span>
        <span class="brand-name__line">Drift</span>
        <span class="brand-name__line brand-name__line--spirit">Vodka</span>
      </h1>

      <svg class="stripe-block stripe-block--ticks" viewBox="0 0 134 118" aria-hidden="true">
        <g fill="var(--label-pink-light)">
          <rect x="0" y="0" width="4" height="118"/>
          <rect x="13" y="0" width="4" height="118"/>
          <rect x="26" y="0" width="4" height="118"/>
          <rect x="39" y="0" width="4" height="118"/>
          <rect x="52" y="0" width="4" height="118"/>
          <rect x="65" y="0" width="4" height="118"/>
          <rect x="78" y="0" width="4" height="118"/>
          <rect x="91" y="0" width="4" height="118"/>
          <rect x="104" y="0" width="4" height="118"/>
          <rect x="117" y="0" width="4" height="118"/>
          <rect x="130" y="0" width="4" height="118"/>
        </g>
      </svg>

      <svg class="stripe-block stripe-block--bottom" viewBox="0 0 333 80" aria-hidden="true">
        <defs>
          <linearGradient id="stripeFadeLow" x1="0" y1="0" x2="1" y2="0">
            <stop offset="0" stop-color="var(--stripe-a)"/>
            <stop offset="1" stop-color="var(--stripe-b)"/>
          </linearGradient>
        </defs>
        <g fill="url(#stripeFadeLow)">
          <rect x="0" y="0" width="333" height="5"/>
          <rect x="0" y="15" width="333" height="5"/>
          <rect x="0" y="30" width="333" height="5"/>
          <rect x="0" y="45" width="333" height="5"/>
          <rect x="0" y="60" width="333" height="5"/>
          <rect x="0" y="75" width="333" height="5"/>
        </g>
      </svg>
    </section>
  </main>
</body>
</html>
```